Brake Test Training for Coal Mining

We offer Brake Test Training for Coal Mine workers. It's a legislative requirement that workers who are tasked with performing brake testing have certain competencies to do so. We test Light Vehicles and trailers, Heavy Vehicles and Mobile Mining Equipment like Graders, Scrapers and Dump Trucks.

```html
<!DOCTYPE html>
<html lang="en">
<head>
<meta charset="utf-8">
<title>Summit Operator Training – Billboard</title>
<link rel="stylesheet" href="https://fonts.googleapis.com/css2?family=Bebas+Neue&family=Montserrat:wght@800&display=swap">
<style>
  :root {
    --navy: #0d3a66;
    --yellow: #f3b700;
    --white: #ffffff;
    --board-bg: #f4f4f2;
    --page-bg: #e9edf1;
    --photo-sky: #c9d6de;
    --photo-machine: #d98b1c;
    --photo-ground: #6a6660;
  }
  * { margin: 0; padding: 0; box-sizing: border-box; }
  html, body {
    width: 1200px;
    height: 1095px;
    overflow: hidden;
    background: var(--page-bg);
  }
  .billboard {
    position: absolute;
    left: 40px;
    top: 305px;
    width: 1120px;
    height: 485px;
    background: var(--board-bg);
    overflow: hidden;
    box-shadow: 0 6px 24px rgba(13, 58, 102, 0.18);
  }
  .billboard-shapes,
  .hero-photo {
    position: absolute;
    left: 0;
    top: 0;
    width: 1120px;
    height: 485px;
  }
  .brand {
    position: absolute;
    left: 150px;
    top: 72px;
    display: flex;
    align-items: center;
    gap: 14px;
  }
  .brand-dot {
    width: 44px;
    height: 44px;
    border-radius: 50%;
    background: var(--navy);
  }
  .brand-name {
    font-family: "Montserrat", sans-serif;
    font-weight: 800;
    font-size: 24px;
    letter-spacing: 0.5px;
    color: var(--navy);
  }
  .headline {
    position: absolute;
    left: 60px;
    top: 190px;
    width: 520px;
    text-align: center;
    font-family: "Bebas Neue", sans-serif;
    font-size: 60px;
    line-height: 64px;
  }
  .headline-main { display: block; color: var(--navy); }
  .headline-accent { display: block; color: var(--yellow); }
  .contact {
    position: absolute;
    left: 76px;
    top: 407px;
    display: flex;
    align-items: center;
    gap: 14px;
  }
  .contact-icon {
    width: 54px;
    height: 54px;
    border-radius: 50%;
    background: var(--yellow);
    display: flex;
    align-items: center;
    justify-content: center;
  }
  .contact-number {
    font-family: "Montserrat", sans-serif;
    font-weight: 800;
    font-size: 46px;
    letter-spacing: 1px;
    color: var(--white);
  }
</style>
</head>
<body>
  <main class="billboard">
    <svg class="billboard-shapes" viewBox="0 0 1120 485" aria-hidden="true">
      <path fill="var(--navy)" d="M645 0 C575 120 565 330 715 485 L1120 485 L1120 0 Z"/>
      <path fill="var(--yellow)" d="M668 0 C598 120 588 330 738 485 L1120 485 L1120 0 Z"/>
      <path fill="var(--white)" d="M678 0 C608 120 598 330 748 485 L1120 485 L1120 0 Z"/>
      <path fill="var(--yellow)" d="M490 392 C545 392 578 420 604 485 L580 485 C555 420 530 392 480 392 Z"/>
      <path fill="var(--navy)" d="M0 392 L480 392 C530 392 555 420 580 485 L0 485 Z"/>
    </svg>

    <svg class="hero-photo" viewBox="0 0 1120 485" role="img" aria-label="Photo of a large yellow mining dump truck beside an excavator at an open-cut mine site">
      <defs>
        <linearGradient id="photoTone" x1="0" y1="0" x2="0" y2="1">
          <stop offset="0" stop-color="var(--photo-sky)"/>
          <stop offset="0.45" stop-color="var(--photo-machine)"/>
          <stop offset="1" stop-color="var(--photo-ground)"/>
        </linearGradient>
      </defs>
      <path fill="url(#photoTone)" d="M690 0 C620 120 610 330 760 485 L1120 485 L1120 0 Z"/>
    </svg>

    <div class="brand">
      <span class="brand-dot"></span>
      <span class="brand-name">SUMMIT OPERATOR TRAINING</span>
    </div>

    <h1 class="headline">
      <span class="headline-main">Training and Experience</span>
      <span class="headline-accent">You Can Rely On</span>
    </h1>

    <div class="contact">
      <span class="contact-icon">
        <svg width="28" height="28" viewBox="0 0 24 24" aria-hidden="true">
          <path fill="var(--navy)" d="M6.6 10.8a15.1 15.1 0 0 0 6.6 6.6l2.2-2.2a1 1 0 0 1 1-.25 11.4 11.4 0 0 0 3.6.57 1 1 0 0 1 1 1V20a1 1 0 0 1-1 1A17 17 0 0 1 3 4a1 1 0 0 1 1-1h3.5a1 1 0 0 1 1 1c0 1.25.2 2.45.57 3.57a1 1 0 0 1-.25 1z"/>
        </svg>
      </span>
      <span class="contact-number">07 5550 1234</span>
    </div>
  </main>
</body>
</html>
```